Natural Light/Organic/Documentary Photography Business

I like a simple, approachable, feminine, earthy/organic feel. Earth/neutral tones, nothing too loud or obnoxious. I like the watercolor look. I don't want anything too trendy or something I'll get tired of after a couple months. As far as colors, I am much more a fan of cream/taupe/blue/green...not a fan of pink or purple at all.

Target Market(s)

Weddings & Families

Industry/Entity Type

Wedding Photography

Contact Information for Business Card

website, email, phone number

Font styles to use
Other font styles liked:
• Horizontes, Gotham

Colors

Designer to choose colors to be used in the design.

Requirements
Must have
• Website: www.mirelhatchway.com
• Phone: 418.629.5073
• Email: mirel@mirelhatchway.com
Nice to have
• I like the watercolor look but its not necessary. I like simple/earthy tones. Nothing too loud or distracting. Simple & feminine without being too girly. I like an approachable/soft feel.
• Instagram: www.instagram.com/mirelhatchwayphotography/
Should not have
• NO loud colors or design or pattern. I do not want a photo of a camera or lens or anything cheesy like that.

```html
<!DOCTYPE html>
<html lang="en">
<head>
<meta charset="utf-8">
<title>Mirel Hatchway Photography – Business Card</title>
<link rel="stylesheet" href="https://fonts.googleapis.com/css2?family=Open+Sans:wght@300;400;600&display=swap">
<style>
  :root {
    --backdrop: #a7acad;
    --paper: #efeeea;
    --ink-taupe: #7b6b64;
    --ink-dark: #4a4441;
    --shadow: rgba(40, 44, 46, 0.28);
  }
  * { margin: 0; padding: 0; box-sizing: border-box; }
  html, body {
    width: 1200px;
    height: 824px;
    overflow: hidden;
    background: var(--backdrop);
    font-family: "Open Sans", Arial, sans-serif;
  }
  .canvas {
    width: 1200px;
    height: 824px;
    display: flex;
    align-items: center;
    justify-content: center;
    gap: 60px;
  }
  .card {
    position: relative;
    width: 525px;
    height: 300px;
    background: var(--paper);
    box-shadow: 0 14px 30px var(--shadow);
  }
  .wordmark {
    position: absolute;
    text-align: center;
    color: var(--ink-taupe);
  }
  .wordmark__name {
    display: block;
    font-weight: 300;
    font-size: 30px;
    letter-spacing: 1px;
    line-height: 1;
  }
  .wordmark__tag {
    display: block;
    margin-top: 6px;
    font-weight: 300;
    font-size: 8px;
    letter-spacing: 5px;
  }
  .card--front .wordmark { top: 38px; right: 36px; }
  .card--front .wordmark__name { font-size: 24px; }
  .contact-list {
    position: absolute;
    left: 30px;
    top: 122px;
    list-style: none;
    color: var(--ink-dark);
    font-size: 13px;
    line-height: 19px;
  }
  .contact-list li { display: flex; align-items: center; gap: 8px; }
  .contact-list svg { width: 11px; height: 11px; flex: none; }
  .card-holder {
    position: absolute;
    right: 32px;
    bottom: 30px;
    color: var(--ink-taupe);
    font-weight: 600;
    font-size: 18px;
  }
  .card--back .wordmark { top: 98px; left: 0; right: 0; }
  .card--back .wordmark__name { font-size: 34px; }
  .website {
    position: absolute;
    top: 188px;
    left: 0;
    right: 0;
    text-align: center;
    color: var(--ink-dark);
    font-size: 11px;
    letter-spacing: 2px;
  }
</style>
</head>
<body>
<main class="canvas">
  <section class="card card--front">
    <div class="wordmark">
      <span class="wordmark__name">Mirel Hatchway</span>
      <span class="wordmark__tag">PHOTOGRAPHY</span>
    </div>
    <ul class="contact-list">
      <li>
        <svg viewBox="0 0 12 12" aria-hidden="true"><rect width="12" height="12" rx="2" fill="var(--ink-taupe)"/><path d="M3.5 3h1.6l.6 1.6-.9.7a5 5 0 0 0 1.9 1.9l.7-.9 1.6.6V8.5A1 1 0 0 1 8 9.5 5.5 5.5 0 0 1 2.5 4a1 1 0 0 1 1-1z" fill="var(--paper)"/></svg>
        418.629.5073
      </li>
      <li>
        <svg viewBox="0 0 12 12" aria-hidden="true"><rect width="12" height="12" rx="2" fill="var(--ink-taupe)"/><rect x="2.5" y="3.5" width="7" height="5" fill="none" stroke="var(--paper)" stroke-width="1"/><path d="M2.5 3.5 6 6.3l3.5-2.8" fill="none" stroke="var(--paper)" stroke-width="1"/></svg>
        mirel@mirelhatchway.com
      </li>
      <li>
        <svg viewBox="0 0 12 12" aria-hidden="true"><rect width="12" height="12" rx="2" fill="var(--ink-taupe)"/><circle cx="6" cy="6" r="3.4" fill="none" stroke="var(--paper)" stroke-width="1"/><path d="M2.6 6h6.8M6 2.6c-1.6 2-1.6 4.8 0 6.8M6 2.6c1.6 2 1.6 4.8 0 6.8" fill="none" stroke="var(--paper)" stroke-width=".8"/></svg>
        www.mirelhatchway.com
      </li>
      <li>
        <svg viewBox="0 0 12 12" aria-hidden="true"><circle cx="6" cy="6" r="6" fill="var(--ink-taupe)"/></svg>
        mirelhatchwayphotography
      </li>
    </ul>
    <p class="card-holder">Mirel Hatchway</p>
  </section>

  <section class="card card--back">
    <div class="wordmark">
      <span class="wordmark__name">Mirel Hatchway</span>
      <span class="wordmark__tag">PHOTOGRAPHY</span>
    </div>
    <p class="website">WWW.MIRELHATCHWAY.COM</p>
  </section>
</main>
</body>
</html>
```